Lanternfield Drinks business cards

We need a business card design for our new logo. The company is modern, progressive, professional, yet approachable. The key products are ready to drink bottles and cans of coffee based beverages.
These cards will be a critical part of the first impression made by our sales organization, business development team, and all external facing personnel.
Card can be a vertical or horizontal orientation.

Target Market(s)

Customers, suppliers, business partners

Industry/Entity Type

Business

Contact Information for Business Card

Business cards should feature Company Name and Logo.

Font styles to use
Serif

Colors

Designer to choose colors to be used in the design.

Requirements
Must have
• Strong readability of Name, phone #, mobile number and email address.
• Job title, website url, Street Address, and other details can be secondary level readability.
Nice to have
• High impact, simplistic quality design.
• Ok to utilize the 'H in the box' separate from the company name

```html
<!DOCTYPE html>
<html lang="en">
<head>
<meta charset="utf-8">
<title>Lanternfield Drinks business cards</title>
<link rel="stylesheet" href="https://fonts.googleapis.com/css2?family=Cinzel:wght@400;700&family=Cabin:wght@400;600&display=swap">
<style>
  :root{
    --bg:#ecebe8;
    --card-orange:#f15a2b;
    --panel-orange:#f7941e;
    --panel-edge:#2a1a10;
    --white:#ffffff;
    --ink-orange:#ef5a28;
    --text-font:"Cabin", sans-serif;
    --name-font:"Cinzel", serif;
  }
  *{box-sizing:border-box;margin:0;padding:0}
  html,body{width:1200px;height:900px;overflow:hidden;background:var(--bg)}
  .canvas{position:relative;width:1200px;height:900px}

  .card{position:absolute;box-shadow:0 6px 18px rgba(0,0,0,.18)}

  /* Front card */
  .card-front{left:77px;top:34px;width:588px;height:361px;background:var(--card-orange);color:var(--white);font-family:var(--text-font)}
  .holder-name{position:absolute;left:30px;top:32px;font-family:var(--name-font);font-size:22px;font-weight:400;letter-spacing:.5px}
  .holder-title{position:absolute;left:30px;top:59px;font-size:15px}
  .contact-list{position:absolute;left:30px;top:181px;list-style:none}
  .contact-list li{display:flex;align-items:center;gap:6px;font-size:15.5px;height:21.5px}
  .contact-list svg{width:15px;height:15px;flex:none}
  .address{position:absolute;left:30px;top:281px;font-size:15.5px;line-height:21px}
  .brand-panel{position:absolute;left:260px;top:0;width:328px;height:361px;border-left:1px solid rgba(0,0,0,.25)}
  .brand-panel-inner{position:absolute;left:20px;top:18px;width:286px;height:323px;background:var(--panel-orange);box-shadow:-3px 3px 0 var(--panel-edge);display:flex;align-items:center;justify-content:center;text-align:center}
  .brand-panel-inner .wordmark{font-family:var(--name-font);font-weight:700;font-size:34px;line-height:1.15;color:var(--white)}

  /* Back card */
  .card-back{left:388px;top:505px;width:567px;height:352px;background:var(--white);font-family:var(--text-font)}
  .back-mark{position:absolute;left:236px;top:91px;width:95px;height:94px;border:4px solid var(--ink-orange)}
  .back-wordmark{position:absolute;left:0;right:0;top:200px;text-align:center;font-family:var(--name-font);font-weight:700;font-size:36px;color:var(--ink-orange);letter-spacing:.5px}
  .back-url{position:absolute;left:0;right:0;top:294px;text-align:center;font-size:17px;font-weight:600;color:var(--ink-orange)}
</style>
</head>
<body>
<div class="canvas">

  <section class="card card-front">
    <h1 class="holder-name">Marcus Hale</h1>
    <p class="holder-title">Managing Director</p>

    <ul class="contact-list">
      <li><svg viewBox="0 0 16 16"><rect width="16" height="16" fill="#fff"/><path d="M4 5c0 4 3 7 7 7l1-2-2-1-1 1c-1-.5-2-1.5-2.5-2.5l1-1-1-2z" fill="#f15a2b"/></svg>044-555 210 377</li>
      <li><svg viewBox="0 0 16 16"><rect width="16" height="16" fill="#fff"/><rect x="5" y="3" width="6" height="10" rx="1" fill="none" stroke="#f15a2b" stroke-width="1.4"/></svg>044-555 210 377</li>
      <li><svg viewBox="0 0 16 16"><rect width="16" height="16" fill="#fff"/><rect x="3" y="4.5" width="10" height="7" fill="none" stroke="#f15a2b" stroke-width="1.3"/><path d="M3 4.5l5 4 5-4" fill="none" stroke="#f15a2b" stroke-width="1.3"/></svg>info@lanternfield.com</li>
      <li><svg viewBox="0 0 16 16"><rect width="16" height="16" fill="#fff"/><circle cx="8" cy="8" r="4.6" fill="#f15a2b"/></svg>www.lanternfielddrinks.com</li>
    </ul>

    <p class="address">12345, Address Goes Here<br>Country Name, 123456.</p>

    <div class="brand-panel">
      <div class="brand-panel-inner">
        <span class="wordmark">Lanternfield<br>Drinks</span>
      </div>
    </div>
  </section>

  <section class="card card-back">
    <div class="back-mark"></div>
    <p class="back-wordmark">Lanternfield Drinks</p>
    <p class="back-url">www.lanternfielddrinks.com</p>
  </section>

</div>
</body>
</html>
```